We have a company that provide sandblasted stone products. Example: numbers for houses. Also we sell cultured stone,brick natural stone to the contractor,homeowner. We need to get a business card that describe our product and service. In the original idea we had an old fashion chisel striking through the x in velquarin.

Reason: We realized that 2 days was not enough time for the competion to be open many of the designers may be to busy and require more time to compete.

Industry/Entity Type

It Company

Logo Text

Velquarin

```html
<!DOCTYPE html>
<html lang="en">
<head>
<meta charset="utf-8">
<title>Velquarin Business Card</title>
<link rel="stylesheet" href="https://fonts.googleapis.com/css2?family=Arimo:wght@400;700&display=swap">
<style>
  :root {
    --page-bg: #eceef0;
    --card-bg: #ffffff;
    --teal-dark: #2f7f97;
    --teal-mid: #3f9cb9;
    --teal-light: #5fc0e2;
    --name-teal: #3d93ae;
    --ink: #1f2426;
    --ink-soft: #3a4044;
    --mark-faint: #f1f5f7;
    --card-shadow: 0 6px 18px rgba(30, 40, 50, 0.18);
  }
  * { box-sizing: border-box; margin: 0; padding: 0; }
  html, body {
    width: 1200px;
    height: 900px;
    overflow: hidden;
    background: var(--page-bg);
    font-family: "Arimo", Arial, sans-serif;
  }
  .canvas {
    width: 1200px;
    height: 900px;
    display: flex;
    flex-direction: column;
    align-items: center;
    justify-content: center;
    gap: 36px;
  }
  .card {
    position: relative;
    width: 700px;
    height: 400px;
    background: var(--card-bg);
    box-shadow: var(--card-shadow);
    overflow: hidden;
  }

  /* Back side: contact details */
  .card-back .accent-band {
    position: absolute;
    inset: 0;
    width: 100%;
    height: 100%;
  }
  .card-back .faint-disc {
    position: absolute;
    right: 60px;
    top: 40px;
    width: 300px;
    height: 300px;
    border-radius: 50%;
    background: var(--mark-faint);
  }
  .contact-list {
    position: absolute;
    left: 38px;
    top: 34px;
    list-style: none;
    font-size: 15px;
    line-height: 1.22;
    color: var(--ink);
  }
  .person {
    position: absolute;
    right: 40px;
    bottom: 46px;
    text-align: right;
  }
  .person-name {
    font-size: 26px;
    color: var(--name-teal);
    line-height: 1.1;
  }
  .person-role {
    font-size: 15px;
    color: var(--ink-soft);
    margin-top: 2px;
  }

  /* Front side: brand name */
  .card-front {
    display: flex;
    align-items: center;
    justify-content: center;
  }
  .brand {
    display: flex;
    align-items: center;
    gap: 18px;
  }
  .brand-dot {
    width: 46px;
    height: 46px;
    border-radius: 50%;
    background: var(--teal-mid);
  }
  .brand-name {
    font-size: 56px;
    font-weight: 400;
    letter-spacing: 1px;
    color: var(--teal-dark);
  }
</style>
</head>
<body>
<main class="canvas">
  <section class="card card-back" aria-label="Business card back">
    <svg class="accent-band" viewBox="0 0 700 400" preserveAspectRatio="none" aria-hidden="true">
      <defs>
        <linearGradient id="bandGradient" x1="0" y1="0" x2="1" y2="1">
          <stop offset="0" stop-color="var(--teal-dark)"/>
          <stop offset="1" stop-color="var(--teal-light)"/>
        </linearGradient>
      </defs>
      <polygon points="0,150 430,400 0,400" fill="url(#bandGradient)"/>
    </svg>
    <div class="faint-disc" aria-hidden="true"></div>
    <ul class="contact-list">
      <li>Unit 8</li>
      <li>47 Quarry Lane, Canada</li>
      <li>Tel: 4820 317</li>
      <li>Mob: 4820 964</li>
      <li>Email: marten@velquarin.ca</li>
      <li>www.velquarin.ca</li>
    </ul>
    <div class="person">
      <p class="person-name">Marten Solberg</p>
      <p class="person-role">Chief Executive Officer</p>
    </div>
  </section>

  <section class="card card-front" aria-label="Business card front">
    <div class="brand">
      <span class="brand-dot" aria-hidden="true"></span>
      <span class="brand-name">VELQUARIN</span>
    </div>
  </section>
</main>
</body>
</html>
```